Maple Roster Business Card for recruitment company

We are looking for a Business Card Design that incorporates our personal details and our busines name and logo. We are a specialized search consultancy that recruit Property and Construction professionals.
We would like a business card that stands out and is appealing to the Construction and Property industry as well.

Target Market(s)

people in the construction and property industry

Contact Information for Business Card

Business Name and logo

Font styles to use
Serif

Colors
0094D4
00A9DD
6FCCEA
C7EBF8
E9F6FB

Requirements
Must have
• Business name and logo as well as contact details
Should not have
• No photos of us please

```html
<!DOCTYPE html>
<html lang="en">
<head>
<meta charset="utf-8">
<title>Maple Roster – Business Card</title>
<link href="https://fonts.googleapis.com/css2?family=Josefin+Sans:wght@400&family=Source+Sans+3:wght@300;400;700&display=swap" rel="stylesheet">
<style>
  :root {
    --page: #e4e5e6;
    --navy: #06324a;
    --navy-dark: #042739;
    --navy-light: #0e4660;
    --ink: #0b3147;
    --card-white: #eceef0;
    --ghost: #dcdee1;
    --text-soft: #333d46;
    --white: #ffffff;
  }
  html, body {
    margin: 0;
    padding: 0;
    width: 1200px;
    height: 1200px;
    overflow: hidden;
    background: var(--page);
  }
  .canvas {
    position: relative;
    width: 1200px;
    height: 1200px;
  }
  .card {
    position: absolute;
    left: 263px;
    width: 682px;
    border-radius: 34px;
    overflow: hidden;
  }
  .card-front {
    top: 165px;
    height: 390px;
    background: var(--navy);
  }
  .front-pattern {
    position: absolute;
    inset: 0;
    background:
      repeating-linear-gradient(90deg, rgba(255,255,255,0) 0 40px, rgba(255,255,255,0.025) 40px 78px),
      linear-gradient(90deg, var(--navy-dark) 0%, var(--navy) 50%, var(--navy-light) 100%);
  }
  .front-brand {
    position: absolute;
    left: 80px;
    top: 268px;
    display: flex;
    align-items: center;
    gap: 14px;
  }
  .front-brand-dot {
    width: 48px;
    height: 48px;
    border: 5px solid var(--white);
    border-radius: 50%;
  }
  .front-brand-name {
    font-family: "Source Sans 3", sans-serif;
    font-weight: 400;
    font-size: 20px;
    letter-spacing: 0.03em;
    color: var(--white);
  }
  .card-back {
    top: 654px;
    height: 387px;
    background: var(--card-white);
  }
  .back-ring {
    position: absolute;
    left: 360px;
    top: 123px;
    width: 276px;
    height: 276px;
    border: 26px solid var(--ghost);
    border-radius: 50%;
  }
  .wordmark {
    position: absolute;
    right: 68px;
    top: 58px;
    margin: 0;
    font-family: "Josefin Sans", sans-serif;
    font-weight: 400;
    font-size: 42px;
    line-height: 1;
    letter-spacing: -0.005em;
    text-transform: uppercase;
    color: var(--ink);
  }
  .person {
    position: absolute;
    left: 68px;
    top: 194px;
    font-family: "Source Sans 3", sans-serif;
    color: var(--text-soft);
  }
  .person-name {
    margin: 0 0 2px;
    font-weight: 700;
    font-size: 20.5px;
    color: var(--ink);
  }
  .person-role {
    margin: 0;
    font-weight: 300;
    font-size: 15.5px;
    line-height: 20px;
  }
  .contacts {
    list-style: none;
    margin: 18px 0 0;
    padding: 0;
    font-weight: 300;
    font-size: 15.5px;
    line-height: 19.5px;
  }
  .contacts li {
    display: flex;
    align-items: center;
    gap: 10px;
  }
  .contacts svg {
    width: 13px;
    height: 13px;
    fill: none;
    stroke: var(--ink);
    stroke-width: 1.6;
  }
</style>
</head>
<body>
<main class="canvas">
  <section class="card card-front">
    <div class="front-pattern" role="img" aria-label="Repeating tonal brand pattern on deep navy"></div>
    <div class="front-brand">
      <span class="front-brand-dot"></span>
      <span class="front-brand-name">Maple Roster</span>
    </div>
  </section>

  <section class="card card-back">
    <div class="back-ring" aria-hidden="true"></div>
    <h1 class="wordmark">Maple Roster</h1>
    <div class="person">
      <p class="person-name">Clara Whitfield</p>
      <p class="person-role">Director</p>
      <p class="person-role">Senior Search Consultant</p>
      <ul class="contacts">
        <li>
          <svg viewBox="0 0 16 16" aria-hidden="true"><path d="M3 2h3l1.5 3.5-2 1.2a8 8 0 0 0 3.8 3.8l1.2-2L14 10v3a1 1 0 0 1-1 1A11 11 0 0 1 2 3a1 1 0 0 1 1-1z"/></svg>
          <span>+64 21 555 0142</span>
        </li>
        <li>
          <svg viewBox="0 0 16 16" aria-hidden="true"><rect x="1.5" y="3.5" width="13" height="9"/><path d="M1.5 3.5 8 9l6.5-5.5"/></svg>
          <span>clara@mapleroster.nz</span>
        </li>
        <li>
          <svg viewBox="0 0 16 16" aria-hidden="true"><circle cx="8" cy="8" r="6.5"/><ellipse cx="8" cy="8" rx="2.8" ry="6.5"/><path d="M1.5 8h13"/></svg>
          <span>www.mapleroster.nz</span>
        </li>
      </ul>
    </div>
  </section>
</main>
</body>
</html>
```